Design concept Visual UI of future mobile app - healthcare

Hi,
I'm looking for a top designer, innovative with strong experience in user interface

The app will be connected to a future health website related to depression and addiction by helping the user to track the moods, tired, anxiety using this mobile app.

I attached the deck of the overall project but I can send you a specific presentation for the app only

thanks

Target Market(s)

Switzerland, UK, Germany and France

Industry/Entity Type

Mental Health

Logo Text

Health, hope

Font styles to use
Sans Serif

Colors
cee9f5
33a6d7
0692cd
0255a3
3276b5
85abd2

Requirements
Must have
• keep it simple, easy to navigate
• The user should be able to track the moods on a daily basis,
• sleep time, and rate how the feel on the day
• To be able to get information from the sync deck of vexlo
Nice to have
• to be able share this app with a friend

```html
<!DOCTYPE html>
<html lang="en">
<head>
<meta charset="utf-8">
<title>Mood Tracker – What's New Today</title>
<link rel="stylesheet" href="https://fonts.googleapis.com/css2?family=Roboto:wght@300;400;500;700&display=swap">
<style>
  :root {
    --page-bg: #e4e4e2;
    --sky-top: #2f86d8;
    --sky-mid: #5db6ec;
    --sky-low: #a8dbf4;
    --white: #ffffff;
    --time-box: #2f7fd0;
    --mood-1: #ee2f1b;
    --mood-2: #f25c17;
    --mood-3: #f28a1b;
    --mood-4: #efc536;
    --mood-5: #cdb61f;
    --mood-6: #bdb71d;
    --mood-7: #b0b126;
    --mood-8: #a5a935;
    --mood-9: #9c9c4f;
    --mood-10: #8d8266;
    --avatar-tone: #c99a6e;
  }
  * { margin: 0; padding: 0; box-sizing: border-box; }
  html, body {
    width: 1200px; height: 800px; overflow: hidden;
    background: var(--page-bg);
    font-family: "Roboto", sans-serif;
  }
  .app-screen {
    position: absolute; left: 393px; top: 32px;
    width: 414px; height: 736px; overflow: hidden;
    color: var(--white);
  }
  .sky {
    position: absolute; inset: 0;
    background: linear-gradient(180deg, var(--sky-top) 0%, var(--sky-mid) 45%, var(--sky-low) 100%);
  }
  .status-bar {
    position: relative; height: 20px; padding: 0 8px;
    display: flex; align-items: center; justify-content: space-between;
    font-size: 11px; font-weight: 500;
  }
  .status-bar .carrier, .status-bar .battery { display: flex; align-items: center; gap: 4px; }
  .status-bar .time { position: absolute; left: 0; right: 0; text-align: center; }
  .nav-bar {
    position: relative; height: 44px;
    display: flex; align-items: center; justify-content: center;
  }
  .nav-title { font-size: 16px; font-weight: 700; letter-spacing: 0.3px; }
  .nav-left { position: absolute; left: 12px; top: 12px; display: flex; gap: 14px; }
  .nav-right { position: absolute; right: 14px; top: 12px; }
  .avatar {
    position: relative; margin: 4px auto 0; width: 56px; height: 56px;
    border-radius: 8px; border: 2px solid var(--white);
    background: linear-gradient(160deg, #8a5a36, var(--avatar-tone) 60%, #e9d2bd);
  }
  .prompt {
    position: relative; text-align: center; margin-top: 8px;
    font-size: 22px; font-weight: 300;
  }
  .mood-scale {
    position: relative; list-style: none;
    width: 300px; margin: 12px auto 0;
  }
  .mood-scale li {
    height: 36px; display: flex; align-items: center; justify-content: center;
    font-size: 16px; font-weight: 400;
  }
  .m1 { background: var(--mood-1); } .m2 { background: var(--mood-2); }
  .m3 { background: var(--mood-3); } .m4 { background: var(--mood-4); }
  .m5 { background: var(--mood-5); } .m6 { background: var(--mood-6); }
  .m7 { background: var(--mood-7); } .m8 { background: var(--mood-8); }
  .m9 { background: var(--mood-9); } .m10 { background: var(--mood-10); }
  .sleep-time {
    position: relative; margin-top: 14px;
    display: flex; align-items: center; justify-content: center; gap: 5px;
    font-size: 16px; font-weight: 700;
  }
  .sleep-time .label { margin-right: 6px; }
  .time-box {
    background: var(--time-box); border-radius: 4px;
    padding: 3px 6px; font-size: 15px; font-weight: 500;
  }
</style>
</head>
<body>
  <main class="app-screen">
    <div class="sky" role="img" aria-label="Blue sky with soft white clouds"></div>

    <div class="status-bar">
      <span class="carrier">
        <svg width="30" height="6" viewBox="0 0 30 6"><g fill="#fff"><circle cx="3" cy="3" r="2.6"/><circle cx="9" cy="3" r="2.6"/><circle cx="15" cy="3" r="2.6"/></g><g fill="none" stroke="#fff"><circle cx="21" cy="3" r="2.3"/><circle cx="27" cy="3" r="2.3"/></g></svg>
        NOVA
        <svg width="12" height="9" viewBox="0 0 12 9"><path d="M6 9 L0.5 3 A8 8 0 0 1 11.5 3 Z" fill="#fff"/></svg>
      </span>
      <span class="time">4:21 PM</span>
      <span class="battery">100%
        <svg width="24" height="11" viewBox="0 0 24 11"><rect x="0.5" y="0.5" width="20" height="10" rx="2" fill="none" stroke="#fff"/><rect x="2" y="2" width="17" height="7" rx="1" fill="#fff"/><rect x="21.5" y="3.5" width="2" height="4" fill="#fff"/></svg>
      </span>
    </div>

    <header class="nav-bar">
      <div class="nav-left">
        <svg width="20" height="18" viewBox="0 0 20 18"><g stroke="#fff" stroke-width="2.4"><line x1="1" y1="3" x2="19" y2="3"/><line x1="1" y1="9" x2="19" y2="9"/><line x1="1" y1="15" x2="19" y2="15"/></g></svg>
        <svg width="12" height="18" viewBox="0 0 12 18"><polyline points="10,2 3,9 10,16" fill="none" stroke="#fff" stroke-width="1.6"/></svg>
      </div>
      <h1 class="nav-title">WHATS NEW TODAY</h1>
      <div class="nav-right">
        <svg width="12" height="18" viewBox="0 0 12 18"><polyline points="2,2 9,9 2,16" fill="none" stroke="#fff" stroke-width="1.6"/></svg>
      </div>
    </header>

    <div class="avatar" role="img" aria-label="User profile photo"></div>
    <p class="prompt">How do you feel today ?</p>

    <ol class="mood-scale">
      <li class="m1">Insanely Great</li>
      <li class="m2">Great</li>
      <li class="m3">Very good</li>
      <li class="m4">Good</li>
      <li class="m5">Okay</li>
      <li class="m6">So-so</li>
      <li class="m7">Meh</li>
      <li class="m8">Bad</li>
      <li class="m9">Very bad</li>
      <li class="m10">Couldn't be worse</li>
    </ol>

    <div class="sleep-time">
      <span class="label">Sleep Time</span>
      <span class="time-box">08</span>
      <span class="time-box">30</span>
      <span class="time-box">30</span>
    </div>
  </main>
</body>
</html>
```